Super elegant, crisp & clean Business card design required

We recently upgraded our branding - which is on our website - talvendoraphoto.com

I would like a simple, yet elegant, clean business card design please.

The font of my logo is Cinzel - and because of the natural colour - it's best to have this on a black background.

I would like to have the back of the business card - with simply my logo.

PLEASE DO NOT SUBMIT A COMPLICATED / UNCLEAN DESIGN

Industry/Entity Type

Business

Contact Information for Business Card

Talven Doroshko Photography

Font styles to use
Other font styles liked:
• Cinzel

Requirements
Must have
• A backpage with nothing but my logo
• Simple design - stands out
Should not have
• Colour that dont align with my logo
• Over complicated '/ non symmetrical design

```html
<!DOCTYPE html>
<html lang="en">
<head>
<meta charset="utf-8">
<title>Talven Doroshko Photography – Business Card</title>
<link rel="stylesheet" href="https://fonts.googleapis.com/css2?family=Cinzel:wght@400&family=Open+Sans:wght@400;600&display=swap">
<style>
  :root {
    --backdrop: #e5e5e5;
    --card-dark: #232323;
    --card-gold: #85765c;
    --gold: #8a7a5f;
    --gold-light: #9a8868;
    --white: #ffffff;
    --rule: #6f6553;
  }
  * { margin: 0; padding: 0; box-sizing: border-box; }
  html, body {
    width: 1200px;
    height: 900px;
    overflow: hidden;
    background: var(--backdrop);
  }
  .canvas {
    position: relative;
    width: 1200px;
    height: 900px;
  }
  .card {
    position: absolute;
    top: 306px;
    width: 440px;
    height: 271px;
    border-radius: 10px;
    overflow: hidden;
  }
  .card--front { left: 149px; background: var(--card-dark); }
  .card--back { left: 608px; background: var(--card-gold); }

  .brand-name {
    position: absolute;
    font-family: "Cinzel", serif;
    font-weight: 400;
    color: var(--gold);
    text-align: center;
    line-height: 1;
  }
  .card--front .brand-name {
    left: 186px;
    top: 47px;
    width: 228px;
    font-size: 19px;
  }
  .brand-name .brand-sub {
    display: block;
    font-size: 10px;
    letter-spacing: 0.42em;
    margin-top: 4px;
    padding-left: 0.42em;
  }
  .card--back .brand-name {
    left: 0;
    top: 112px;
    width: 100%;
    font-size: 29px;
    color: var(--white);
  }
  .card--back .brand-name .brand-sub {
    font-size: 14px;
    letter-spacing: 0.5em;
    margin-top: 7px;
    padding-left: 0.5em;
  }

  .person {
    position: absolute;
    left: 23px;
    top: 113px;
    font-family: "Open Sans", sans-serif;
  }
  .person-name {
    font-size: 16px;
    font-weight: 600;
    color: var(--gold-light);
    line-height: 20px;
  }
  .person-role {
    font-size: 12px;
    color: var(--white);
    line-height: 15px;
  }
  .divider {
    position: absolute;
    left: 0;
    top: 156px;
    width: 100%;
    height: 1px;
    background: var(--rule);
  }
  .contact {
    position: absolute;
    left: 23px;
    top: 176px;
    list-style: none;
    font-family: "Open Sans", sans-serif;
    font-size: 12px;
    line-height: 18px;
    color: var(--white);
  }
</style>
</head>
<body>
<main class="canvas">
  <section class="card card--front" aria-label="Business card front">
    <p class="brand-name">Talven Doroshko<span class="brand-sub">Photography</span></p>
    <div class="person">
      <p class="person-name">Elias Varrow</p>
      <p class="person-role">Managing Director</p>
    </div>
    <div class="divider"></div>
    <ul class="contact">
      <li>(044)-456-7890 &nbsp;|&nbsp; 123-456-7890</li>
      <li>hello@talvendoraphoto.com</li>
      <li>www.talvendoraphoto.com</li>
      <li>12345, Address Goes Here Country Name, 123456</li>
    </ul>
  </section>

  <section class="card card--back" aria-label="Business card back">
    <p class="brand-name">Talven Doroshko<span class="brand-sub">Photography</span></p>
  </section>
</main>
</body>
</html>
```